5KO Outings

Explain what 5KO means ( Water, Wave, Wake Expereince)
We offer surfing, wake baording, water skliing on a state of the art surf and equipment all included in the charter. The captain is a Norvane Shore Watch captain.
We offer wake surfing, wakeboarding, water skiing, tubing. We have state of the art video with 3 cameras onboard 2,360 view camers for videioing your day on the water.
Located on the Delta, serving Lake Tahoe in the summer time, Lake Berryasea, and other local lakes.
We specliaize in birthday parties, bacholer, bachlorrete, graduation parties and team building events.

Target Market(s)

Indivuals, business, wedding and event planners

Industry/Entity Type

Water sports

Requirements
Must have
• My logo,
Nice to have
• Simple, not to busy

```html
<!DOCTYPE html>
<html lang="en">
<head>
<meta charset="utf-8">
<title>5KO Outings – Water Wave Wake Experience</title>
<link href="https://fonts.googleapis.com/css2?family=Montserrat:ital,wght@0,700;0,800;0,900;1,800;1,900&family=Oswald:wght@500;600&family=Roboto+Condensed:ital,wght@0,700;0,900;1,400;1,700;1,900&display=swap" rel="stylesheet">
<style>
:root{
  --backdrop:#0a1a3a;
  --navy:#1d2947;
  --navy-deep:#16203a;
  --cyan:#3cc4d8;
  --cyan-bright:#3fd6e6;
  --lime:#b6e03a;
  --orange:#cf4a1a;
  --white:#ffffff;
  --sky-warm:#f4c89a;
  --sky-blue:#8fc4e4;
  --sea:#1d7fc0;
}
*{margin:0;padding:0;box-sizing:border-box}
html,body{width:1200px;height:1200px;overflow:hidden}
body{background:var(--backdrop);font-family:"Roboto Condensed",sans-serif}
.flyer{position:absolute;left:150px;top:18px;width:900px;height:1164px;background:var(--white);overflow:hidden}
.abs{position:absolute}
.sky{left:0;top:0;width:900px;height:300px;background:linear-gradient(180deg,#e9c9a8 0%,var(--sky-warm) 20%,#cfd9e6 55%,rgba(255,255,255,0) 100%)}
.brand{left:70px;top:96px;width:290px;text-align:center}
.brand-name{font-family:"Montserrat",sans-serif;font-weight:900;font-size:40px;color:var(--navy);letter-spacing:1px}
.brand-tag{margin-top:20px;font-family:"Montserrat",sans-serif;font-weight:800;font-size:14.5px;color:var(--navy)}
.headline{left:57px;top:210px;font-family:"Montserrat",sans-serif;font-style:italic;font-weight:900;line-height:1}
.headline .l1{font-size:44px;color:var(--cyan)}
.headline .l2{font-size:32px;color:var(--cyan);margin-top:2px}
.headline .l3{font-size:104px;color:var(--navy);font-style:normal;letter-spacing:-3px;margin-top:-2px}
.sea-band{left:0;top:397px;width:460px;height:146px;background:linear-gradient(90deg,#1a6db0,var(--sea) 50%,#2a9ad6)}
.tagline{left:60px;top:408px;font-family:"Montserrat",sans-serif;font-style:italic;font-weight:900;font-size:34px;line-height:1.12;color:var(--white)}
.tagline .lower{font-weight:800}
.offer-panel{left:0;top:541px;width:505px;height:172px;background:var(--navy);border-bottom-right-radius:70px}
.offer-title{left:60px;top:563px;font-family:"Montserrat",sans-serif;font-style:italic;font-weight:900;font-size:30px;color:var(--lime)}
.offer-list{left:60px;top:608px;display:grid;grid-template-columns:226px 200px;row-gap:8px;list-style:none}
.offer-list li{display:flex;align-items:center;gap:9px;font-family:"Montserrat",sans-serif;font-style:italic;font-weight:800;font-size:22px;color:var(--white)}
.offer-list svg{flex:none}
.charter-pill{left:54px;top:697px;width:412px;height:33px;border-radius:17px;background:var(--orange);color:var(--white);display:flex;align-items:center;justify-content:center;gap:10px;font-style:italic;font-size:21px}
.charter-pill .star{color:var(--navy);font-size:15px;font-style:normal}
.hero{left:0;top:0;width:900px;height:760px}
.hero-title{left:638px;top:146px;font-family:"Roboto Condensed",sans-serif;font-style:italic;font-weight:900;font-size:72px;line-height:0.95;color:var(--cyan-bright)}
.hero-sub{left:637px;top:352px;font-family:"Oswald",sans-serif;font-weight:500;font-size:56px;line-height:1.2;color:var(--white);transform:scaleX(0.74);transform-origin:left top;white-space:nowrap}
.captain-badge{left:528px;top:632px;width:94px;height:94px}
.captain-head{left:634px;top:630px;font-style:italic;font-weight:900;font-size:30px;line-height:1;color:var(--navy)}
.captain-head .hl{color:var(--cyan);display:block}
.captain-note{left:634px;top:697px;font-style:italic;font-size:14px;line-height:1.15;color:var(--navy)}
.bottom-sea{left:0;top:880px;width:900px;height:284px;background:linear-gradient(180deg,#7aa9c6 0%,#4f86a8 40%,#6f9fbc 75%,#e8eff4 100%)}
.card{top:756px;width:186px;height:311px}
.card-photo{width:186px;height:124px;border-radius:36px 36px 0 0}
.card-body{height:187px;background:var(--navy);border-radius:0 0 90px 90px;text-align:center;padding-top:12px;color:var(--white)}
.card-title{font-style:italic;font-weight:900;font-size:25px;line-height:0.98;color:var(--cyan);text-transform:uppercase}
.card-text{margin-top:10px;font-style:italic;font-size:12.5px;line-height:1.13}
.card-chip{display:inline-block;margin-top:5px;background:var(--lime);color:var(--navy);border-radius:8px;padding:1px 8px;font-style:italic;font-size:12px}
.card-serving{display:block;margin-top:7px;color:var(--cyan);font-style:italic;font-size:12.5px}
.card-serving + .card-text{margin-top:0}
.book-blob{left:660px;top:756px;width:188px;height:118px;background:var(--lime);border-radius:22px 14px 30px 8px;transform:rotate(-2deg)}
.book-text{left:670px;top:770px;font-style:italic;font-weight:900;font-size:30px;line-height:0.92;color:var(--navy);transform:rotate(-2deg)}
.book-today{left:695px;top:836px;width:148px;height:56px;background:var(--orange);border-radius:10px;transform:rotate(-3deg);color:var(--white);font-style:italic;font-weight:900;font-size:36px;display:flex;align-items:center;justify-content:center}
.footer-pill{top:1096px;height:36px;border-radius:18px;background:var(--navy);display:flex;align-items:center;color:var(--white);font-style:italic;font-weight:900}
.follow{left:36px;width:184px;background:var(--lime);border:2px solid var(--navy);overflow:hidden}
.follow .label{background:var(--orange);height:100%;width:104px;border-radius:0 18px 18px 0;display:flex;align-items:center;justify-content:center;font-size:17px}
.phone{left:244px;width:232px;font-size:29px;gap:12px;padding-left:8px}
.web{left:497px;width:366px;font-size:29px;gap:10px;padding-left:8px}
.icon-dot{width:28px;height:28px;border-radius:50%;background:var(--lime);display:flex;align-items:center;justify-content:center;flex:none}
</style>
</head>
<body>
<main class="flyer">
  <div class="abs sky" role="img" aria-label="Sunset sky over the water"></div>

  <div class="abs brand">
    <div class="brand-name">5KO Outings</div>
    <div class="brand-tag">SURF IT, LAUNCH IT, CARVE IT!</div>
  </div>

  <h1 class="abs headline">
    <div class="l1">RIDE THE</div>
    <div class="l2">WAVES WITH</div>
    <div class="l3">5KO</div>
  </h1>

  <div class="abs sea-band" role="img" aria-label="Open blue sea"></div>
  <p class="abs tagline"><span class="lower">Unforgettable</span><br>ADVENTURES<br>ON THE WATER!</p>

  <div class="abs offer-panel"></div>
  <h2 class="abs offer-title">WHAT WE OFFER:</h2>
  <ul class="abs offer-list">
    <li><svg width="17" height="17" viewBox="0 0 17 17"><circle cx="8.5" cy="8.5" r="7.5" fill="none" stroke="var(--cyan)" stroke-width="1.6"/><path d="M5 8.8l2.4 2.3L12 6.3" fill="none" stroke="var(--cyan)" stroke-width="1.6"/></svg>Wake Surfing</li>
    <li><svg width="17" height="17" viewBox="0 0 17 17"><circle cx="8.5" cy="8.5" r="7.5" fill="none" stroke="var(--cyan)" stroke-width="1.6"/><path d="M5 8.8l2.4 2.3L12 6.3" fill="none" stroke="var(--cyan)" stroke-width="1.6"/></svg>Tubing</li>
    <li><svg width="17" height="17" viewBox="0 0 17 17"><circle cx="8.5" cy="8.5" r="7.5" fill="none" stroke="var(--cyan)" stroke-width="1.6"/><path d="M5 8.8l2.4 2.3L12 6.3" fill="none" stroke="var(--cyan)" stroke-width="1.6"/></svg>Wakeboarding</li>
    <li><svg width="17" height="17" viewBox="0 0 17 17"><circle cx="8.5" cy="8.5" r="7.5" fill="none" stroke="var(--cyan)" stroke-width="1.6"/><path d="M5 8.8l2.4 2.3L12 6.3" fill="none" stroke="var(--cyan)" stroke-width="1.6"/></svg>Water Skiing</li>
  </ul>
  <div class="abs charter-pill"><span class="star">★</span>All equipment included in the charter<span class="star">★</span></div>

  <svg class="abs hero" viewBox="0 0 900 760">
    <defs>
      <radialGradient id="wakeSpray" cx="0.5" cy="0.45" r="0.6">
        <stop offset="0" stop-color="#3fa9c4"/>
        <stop offset="0.6" stop-color="#17708f"/>
        <stop offset="1" stop-color="#0e4f6b"/>
      </radialGradient>
      <linearGradient id="sunsetRide" x1="0" y1="0" x2="0" y2="1">
        <stop offset="0" stop-color="#e6a878"/><stop offset="1" stop-color="#8a8f86"/>
      </linearGradient>
      <linearGradient id="yachtDeck" x1="0" y1="0" x2="0" y2="1">
        <stop offset="0" stop-color="#9cc6e6"/><stop offset="1" stop-color="#e4eaf0"/>
      </linearGradient>
      <linearGradient id="tubeRide" x1="0" y1="0" x2="0" y2="1">
        <stop offset="0" stop-color="#4a88ad"/><stop offset="1" stop-color="#d98a86"/>
      </linearGradient>
    </defs>
    <circle cx="654" cy="317" r="283" fill="var(--navy)"/>
    <circle cx="654" cy="317" r="262" fill="var(--white)"/>
    <circle cx="654" cy="317" r="250" fill="url(#wakeSpray)" role="img" aria-label="Wake surfer in a wetsuit riding behind a boat"/>
    <circle cx="442" cy="336" r="92" fill="var(--navy)"/>
    <circle cx="442" cy="336" r="86" fill="var(--cyan)"/>
    <circle cx="442" cy="336" r="82" fill="url(#sunsetRide)" role="img" aria-label="Wakeboarder jumping at sunset"/>
    <circle cx="503" cy="535" r="95" fill="var(--navy)"/>
    <circle cx="503" cy="535" r="89" fill="var(--cyan)"/>
    <circle cx="503" cy="535" r="85" fill="url(#yachtDeck)" role="img" aria-label="Deck of a white charter boat on the sea"/>
    <circle cx="740" cy="528" r="95" fill="var(--navy)"/>
    <circle cx="740" cy="528" r="89" fill="var(--cyan)"/>
    <circle cx="740" cy="528" r="85" fill="url(#tubeRide)" role="img" aria-label="Rider relaxing on an inflatable tube"/>
  </svg>

  <h2 class="abs hero-title">Water<br>Wave<br>Wake</h2>
  <div class="abs hero-sub">EXPEREINCE</div>

  <svg class="abs captain-badge" viewBox="0 0 94 94">
    <circle cx="47" cy="47" r="45" fill="var(--navy)"/>
    <circle cx="47" cy="47" r="38" fill="var(--lime)"/>
  </svg>
  <h3 class="abs captain-head">EXPERT SHORE<span class="hl">WATCH CAPTAIN</span></h3>
  <p class="abs captain-note">Led by a Norvane-certified professional<br>for a safe and thrilling ride.</p>

  <div class="abs bottom-sea" role="img" aria-label="Lake water with a wakeboarder carving behind the boat"></div>

  <article class="abs card" style="left:43px">
    <div class="card-photo" style="background:linear-gradient(180deg,#9fb4c4,#546a7a)" role="img" aria-label="Phone on a gimbal filming the lake"></div>
    <div class="card-body">
      <h4 class="card-title">Pro-Level<br>Video<br>Recording</h4>
      <p class="card-text">3 onboard cameras,<br>including two 360° view<br>camera, to capture<br>every epic moment.</p>
    </div>
  </article>
  <article class="abs card" style="left:244px">
    <div class="card-photo" style="background:linear-gradient(180deg,#7fb1dc,#3f6e3a 60%,#6d8a9c)" role="img" aria-label="River delta between green hills"></div>
    <div class="card-body">
      <h4 class="card-title">Prime<br>Locations</h4>
      <span class="card-chip">Based on the Delta</span>
      <span class="card-serving">SERVING</span>
      <p class="card-text">Lake Tahoe (summer),<br>Lake Berryessa,<br>and other local lakes.</p>
    </div>
  </article>
  <article class="abs card" style="left:438px">
    <div class="card-photo" style="background:linear-gradient(180deg,#5f8fb8,#c9a6b0 60%,#d8dde2)" role="img" aria-label="Friends celebrating with balloons on a boat"></div>
    <div class="card-body">
      <h4 class="card-title">Perfect<br>for Special<br>Events</h4>
      <p class="card-text">Birthday parties,<br>bachelor/bachelorette<br>parties, graduations, &amp;<br>team-building events.</p>
    </div>
  </article>

  <div class="abs book-blob"></div>
  <div class="abs book-text">BOOK YOUR<br>ADVENTURE</div>
  <div class="abs book-today">TODAY!</div>

  <div class="abs footer-pill follow"><span class="label">FOLLOW US</span></div>
  <div class="abs footer-pill phone">
    <span class="icon-dot"><svg width="16" height="16" viewBox="0 0 24 24"><path d="M6.6 10.8a15 15 0 006.6 6.6l2.2-2.2a1 1 0 011-.25 11.4 11.4 0 003.6.57 1 1 0 011 1V20a1 1 0 01-1 1A17 17 0 013 4a1 1 0 011-1h3.5a1 1 0 011 1c0 1.25.2 2.45.57 3.6a1 1 0 01-.25 1z" fill="var(--navy)"/></svg></span>
    555 014 7788
  </div>
  <div class="abs footer-pill web">
    <span class="icon-dot"><svg width="18" height="18" viewBox="0 0 24 24" fill="none" stroke="var(--navy)" stroke-width="1.8"><circle cx="12" cy="12" r="9"/><ellipse cx="12" cy="12" rx="4" ry="9"/><path d="M3 12h18M5 7h14M5 17h14"/></svg></span>
    www.5kooutings.com
  </div>
</main>
</body>
</html>
```